Black Car Limousine transportation business in Naples Florida

Always stand for my reliability and RVD stands for Love, K and M are the first initials of my children's names. It should show professionalism and a dedication to customer service. We keep our clients identities private. Show our professionalism. We are Black car Black tie company. We service transportation on a reserve basis to and from residents, airports, casinos, hotels,

Target Market(s)

It is a Private car service. High end clients. Businesses, Celebrity and athletes. Service to airports, hotels, special events.

Industry/Entity Type

Business

Contact Information for Business Card

A pearl metallic or Luster card. Standard business card size. Would like the name, Company email, show we take credit cards and phone number. Currently I don't have a website but will like to add later.

Logo Text

STEADFAST RVD TRANSPORTATION

Font styles to use
Serif

Colors
eaeaea
000000

Requirements
Must have
• Must have Company email, show we take credit cards and phone number. Currently I don't have a website but will like to add later.
Nice to have
• Would like to stay with a black and white theme. Open to some color trim.
Should not have
• Open to suggestions

```html
<!DOCTYPE html>
<html lang="en">
<head>
<meta charset="utf-8">
<title>Steadfast RVD Transportation – Business Card</title>
<link rel="stylesheet" href="https://fonts.googleapis.com/css2?family=EB+Garamond:ital,wght@0,500;0,600;0,700;1,700&display=swap">
<style>
  :root {
    --board: #c4c4c4;
    --card: #ffffff;
    --ink: #000000;
    --paper-text: #ffffff;
    --photo-dark: #1c1c1c;
    --photo-light: #5a5a5a;
  }
  * { margin: 0; padding: 0; box-sizing: border-box; }
  html, body {
    width: 1105px; height: 1200px; overflow: hidden;
    background: var(--board);
    font-family: "EB Garamond", Georgia, serif;
  }
  .canvas { position: relative; width: 1105px; height: 1200px; }
  .card {
    position: absolute; left: 193px; width: 720px; height: 410px;
    background: var(--card); overflow: hidden;
  }
  .card-front { top: 167px; }
  .card-back { top: 623px; }

  .brand {
    position: absolute; left: 44px; top: 54px;
    color: var(--ink); font-weight: 600; line-height: 1.1;
    font-size: 30px; letter-spacing: 1px;
  }
  .brand span { display: block; font-size: 19px; letter-spacing: 3.4px; }

  .vehicle-band {
    position: absolute; left: 0; top: 185px; width: 720px; height: 225px;
    background: var(--ink);
  }

  .holder { position: absolute; left: 48px; top: 312px; color: var(--paper-text); }
  .holder-name { font-size: 27px; font-weight: 600; letter-spacing: .5px; line-height: 1.1; }
  .holder-title { font-size: 20px; font-weight: 500; line-height: 1.4; }

  .contacts {
    position: absolute; right: 50px; top: 288px;
    list-style: none; color: var(--paper-text); font-size: 20px; font-weight: 500; text-align: right;
  }
  .contacts li { display: flex; align-items: center; justify-content: flex-end; gap: 10px; height: 28px; }
  .contacts svg { width: 18px; height: 18px; fill: var(--paper-text); }

  .vehicle-photo {
    position: absolute; left: 152px; top: 131px; width: 387px; height: 156px;
    border-radius: 12px;
    background: linear-gradient(180deg, var(--photo-light) 0%, var(--photo-dark) 55%, var(--ink) 100%);
  }
  .payment-note {
    position: absolute; left: 228px; top: 332px;
    display: flex; align-items: center; gap: 8px;
    font-size: 21px; font-weight: 700; font-style: italic; color: var(--ink);
  }
  .payment-note svg { width: 28px; height: 22px; }
</style>
</head>
<body>
<div class="canvas">

  <section class="card card-front">
    <div class="brand">STEADFAST RVD<span>TRANSPORTATION</span></div>

    <div class="vehicle-band" role="img" aria-label="Black silhouette illustration of a luxury SUV with a silver outline"></div>

    <div class="holder">
      <p class="holder-name">MARCUS HALE</p>
      <p class="holder-title">CEO/Founder</p>
    </div>

    <ul class="contacts">
      <li>555 014 2273
        <svg viewBox="0 0 24 24" aria-hidden="true"><path d="M6.6 10.8a15.1 15.1 0 0 0 6.6 6.6l2.2-2.2a1 1 0 0 1 1-.25 11.4 11.4 0 0 0 3.6.57 1 1 0 0 1 1 1V20a1 1 0 0 1-1 1A17 17 0 0 1 3 4a1 1 0 0 1 1-1h3.5a1 1 0 0 1 1 1c0 1.25.2 2.45.57 3.57a1 1 0 0 1-.25 1z"/></svg>
      </li>
      <li>ride@steadfastrvd.com
        <svg viewBox="0 0 24 24" aria-hidden="true"><path d="M2 5h20v14H2z"/><path d="M3 6.5 12 13l9-6.5" fill="none" stroke="var(--ink)" stroke-width="1.6"/></svg>
      </li>
      <li>www.steadfastrvd.com
        <svg viewBox="0 0 24 24" aria-hidden="true"><circle cx="12" cy="12" r="10"/><path d="M2 12h20M12 2c3 3 3 17 0 20M12 2c-3 3-3 17 0 20" fill="none" stroke="var(--ink)" stroke-width="1.6"/></svg>
      </li>
    </ul>
  </section>

  <section class="card card-back">
    <div class="vehicle-photo" role="img" aria-label="Photograph of a black luxury SUV"></div>
    <p class="payment-note">
      <svg viewBox="0 0 28 22" aria-hidden="true"><rect x="1" y="3" width="26" height="16" rx="2" fill="var(--ink)"/><rect x="1" y="7" width="26" height="3" fill="var(--card)"/><rect x="16" y="13" width="7" height="3" fill="var(--card)"/></svg>
      We accept credit cards
    </p>
  </section>

</div>
</body>
</html>
```